Flyer Vacation Gift Certificate

I need to create a beautiful flyer 8.5 x 11 PDF format flyer design. <br/><br/>Instructions:<br/>The flyer will really be a gift voucher for a las vegas vacation getaway. So must have a Las Vegas Theme exciting fun<br/><br/>The voucher should have two modules that will be editable. <br/>Must have a "Compliments Of" area and also must have an "Exclusively For" area<br/><br/>Keep in mind that this flyer will be printed so keep that in mind :)<br/><br/>Here the is the content for the vacation voucher:<br/><br/>There is no doubt that Las Vegas is one of the hottest travel destinations around the world. In fact, some people would even go as far as<br/>saying that perhaps it is THE hottest place to visit. Enjoy up to 4 nights of resort/casino accommodations in exciting Las Vegas, NV. Millions of people travel to this exciting city each year to enjoy its thrills. Thanks to the business you received this certificate from, now you can enjoy exciting Las Vegas, NV too!<br/><br/>Features:<br/>*Travel 7 Days A Week<br/>*Stay Your Choice Of Nights (1-4 Nights)<br/>*Good For Two Adults & Two Children<br/>*Pay Just The Taxes & Fees<br/>*Multiple Travel Date Requests Allowed<br/>*Fully Transferable To Another Person<br/>*Just A 30 Days Advance Notice Required<br/>*You Will Have 12 Months To Complete Travel After Redemption<br/><br/>HOW CAN WE DO THIS?<br/><br/>We contract with the world leading hotel chains and resorts to help them fill their otherwise empty rooms.<br/><br/>We help fill empty rooms which the hotels, resorts and cruise lines turn into additional revenue from other areas of their property and future bookings.<br/><br/>Hotels rarely experience full occupancy, yet they remain open, providing rooms and services at fixed costs. So when hotels give out their rooms by partnering with marketing companies like us, they might miss out on the room fee, but they already didn't have that in the first place, at least now they have the opportunity to gain a customer for their in-house restaurants, room service, their casinos, an extra day stay, future bookings, etc.<br/><br/>VIEW ALL THE DETAILS OF THIS SPECIAL OFFER AND REDEEM ONLINE AT <br/>WWW.QOTAVERNIX.COM<br/><br/>Certificate ID # 47261-38157<br/>Expires 02/29/2020<br/><br/><br/>*terms and conditions apply see website for details<br/><br/>KEEP IN MIND THE EXAMPLES I AM UPLOADING ARE SIMPLY TO SHOW YOU THAT THEY CONTAIN THE "COMPLIMENTS OF" AND "EXCLUSIVELY FOR" ELEMENTS. THESE MUST BE INCLUDED IN NEW DESIGN. PLEASE ONLY USE THE CONTENT I PROVIDED IN BRIEF, DONT USE CONTENT FROM EXAMPLES.

Target Market(s)

CONSUMERS THAT HAVE BEEN REWARDED WITH A VACATION CERTIFICATE FOR DOING BUSINESS WITH A COMPANY.

COMPANIES USE THESE AS MARKETING INCENTIVES TO ATTRACT MORE CUSTOMERS AND TO REWARD LOYALTY, ETC.

Industry/Entity Type

Travel Industry

Colors

Designer to choose colors to be used in the design.

Requirements
Must have
• I need to create a beautiful flyer 8.5 x 11 PDF format flyer design.
• Instructions:
• The flyer will really be a gift voucher for a las vegas vacation getaway. So must have a Las Vegas Theme exciting fun
• The voucher should have two modules that will be editable.
• Must have a "Compliments Of" area and also must have an "Exclusively For" area
• Keep in mind that this flyer will be printed so keep that in mind :)
• Here the is the content for the vacation voucher:
• There is no doubt that Las Vegas is one of the hottest travel destinations around the world. In fact, some people would even go as far as
• saying that perhaps it is THE hottest place to visit. Enjoy up to 4 nights of resort/casino accommodations in exciting Las Vegas, NV. Millions of people travel to this exciting city each year to enjoy its thrills. Thanks to the business you received this certificate from, now you can enjoy exciting Las Vegas, NV too!
• Features:
• *Travel 7 Days A Week
• *Stay Your Choice Of Nights (1-4 Nights)
• *Good For Two Adults & Two Children
• *Pay Just The Taxes & Fees
• *Multiple Travel Date Requests Allowed
• *Fully Transferable To Another Person
• *Just A 30 Days Advance Notice Required
• *You Will Have 12 Months To Complete Travel After Redemption
• HOW CAN WE DO THIS?
• We contract with the world leading hotel chains and resorts to help them fill their otherwise empty rooms.
• We help fill empty rooms which the hotels, resorts and cruise lines turn into additional revenue from other areas of their property and future bookings.
• Hotels rarely experience full occupancy, yet they remain open, providing rooms and services at fixed costs. So when hotels give out their rooms by partnering with marketing companies like us, they might miss out on the room fee, but they already didn't have that in the first place, at least now they have the opportunity to gain a customer for their in-house restaurants, room service, their casinos, an extra day stay, future bookings, etc.
• VIEW ALL THE DETAILS OF THIS SPECIAL OFFER AND REDEEM ONLINE AT
• WWW.QOTAVERNIX.COM
• Certificate ID # 47261-38157
• Expires 02/29/2020
• *terms and conditions apply see website for details
• KEEP IN MIND THE EXAMPLES I AM UPLOADING ARE SIMPLY TO SHOW YOU THAT THEY CONTAIN THE "COMPLIMENTS OF" AND "EXCLUSIVELY FOR" ELEMENTS. THESE MUST BE INCLUDED IN NEW DESIGN. PLEASE ONLY USE THE CONTENT I PROVIDED IN BRIEF, DONT USE CONTENT FROM EXAMPLES.
Nice to have
• EXCITING LAS VEGAS IMAGES THAT MAKE SOMEONE WANT TO GO THERE

```html
<!DOCTYPE html>
<html lang="en">
<head>
<meta charset="utf-8">
<title>Las Vegas Vacation Certificate</title>
<link href="https://fonts.googleapis.com/css2?family=Bebas+Neue&family=Roboto:ital,wght@0,300;0,400;0,500;0,700;1,700;1,900&family=Roboto+Condensed:wght@400;700&display=swap" rel="stylesheet">
<style>
  :root{
    --ink:#111111;
    --night:#0f0f1c;
    --red:#e32b2b;
    --white:#ffffff;
    --gold-dark:#6e5a3e;
    --gold-mid:#c3ad6b;
    --gold-deep:#8a7149;
    --checkbox:#5a4a38;
  }
  *{margin:0;padding:0;box-sizing:border-box}
  html,body{width:927px;height:1200px;overflow:hidden;background:var(--white)}
  .flyer{position:relative;width:927px;height:1200px;font-family:'Roboto',sans-serif;color:var(--ink);overflow:hidden}

  .hero{position:absolute;left:0;top:0;width:927px;height:350px;
    background:linear-gradient(180deg,#2f64b8 0%,#5c8fd0 18%,#3b4d7a 38%,#5a4a52 55%,#c08a3e 75%,#3a3340 100%)}

  .compliments{position:absolute;left:645px;top:51px;width:231px;height:232px;background:var(--white);
    text-align:center;font-weight:700;color:var(--ink)}
  .compliments__title{margin-top:25px;font-size:18.5px;line-height:20px;letter-spacing:.2px}
  .compliments__lines{position:absolute;left:0;right:0;top:156px;font-size:16.5px;line-height:20px;font-weight:500}

  .exclusive{position:absolute;left:0;top:316px;width:357px;height:34px;background:var(--red);
    color:var(--white);font-weight:700;font-size:16.5px;line-height:34px;padding-left:36px;letter-spacing:.2px}

  .headline{position:absolute;left:0;top:350px;width:927px;height:86px;background:var(--night);
    color:var(--white);text-align:center;font-weight:700;font-size:38px;line-height:37px;padding-top:7px;letter-spacing:.4px}

  .gallery__photo{position:absolute;top:447px;width:228px;height:175px;border:4px solid #8f7a4c;border-radius:3px;
    box-shadow:0 8px 8px -4px rgba(0,0,0,.45)}
  .gallery__photo--sign{left:108px;background:radial-gradient(circle at 50% 45%,#d8343f 0%,#6b2a6a 35%,#0d0b18 75%)}
  .gallery__photo--hotel{left:350px;background:linear-gradient(180deg,#0b0d20 0%,#cfd3e0 35%,#e0584a 70%,#3b1d24 100%)}
  .gallery__photo--strip{left:591px;background:linear-gradient(180deg,#0a0c18 0%,#3a2a3a 40%,#d8562e 70%,#401818 100%)}

  .section-title{position:absolute;left:37px;font-family:'Bebas Neue',sans-serif;font-size:37px;line-height:34px;color:var(--ink)}
  .section-title--features{top:653px}
  .section-title--how{top:832px}

  .features{position:absolute;left:39px;top:691px;list-style:none;font-size:12px;font-weight:300;line-height:15.2px;color:#222}
  .features li{display:flex;align-items:center}
  .features li::before{content:"";width:11px;height:11px;margin-right:9px;border:2px solid var(--checkbox);
    background:radial-gradient(var(--checkbox) 0 45%,var(--white) 46%)}

  .reasons{position:absolute;left:38px;top:872px;width:450px;list-style:none}
  .reasons li{display:flex;font-size:11.6px;line-height:12.1px;color:#222;margin-bottom:9px}
  .reasons svg{flex:none;width:24px;height:22px;margin-right:2px;margin-top:1px}

  .cta{position:absolute;left:60px;top:1035px;width:406px;text-align:center}
  .cta__lead{font-family:'Roboto Condensed',sans-serif;font-weight:700;font-size:17.5px;letter-spacing:-.3px}
  .cta__link{font-weight:900;font-style:italic;font-size:25px;line-height:27px;letter-spacing:-.6px}

  .story{position:absolute;left:524px;top:632px;width:352px;height:492px;
    background:linear-gradient(180deg,var(--gold-dark) 0%,var(--gold-mid) 40%,var(--gold-mid) 60%,var(--gold-deep) 100%)}
  .story__text{margin:33px 22px 0;text-align:center;color:var(--white);font-weight:500;font-size:18.6px;line-height:24.3px}

  .certificate{position:absolute;left:43px;top:407px;width:266px;height:68px;background:var(--white);text-align:center;color:var(--ink)}
  .certificate__id{font-family:'Roboto Condensed',sans-serif;font-weight:700;font-size:17px;line-height:19px;margin-top:6px}
  .certificate__terms{font-family:'Roboto Condensed',sans-serif;font-size:10.5px;letter-spacing:-.3px;margin-top:3px}

  .footer{position:absolute;left:0;top:1124px;width:927px;height:76px;background:var(--night);
    color:var(--white);text-align:center;font-weight:300;font-size:21px;line-height:76px;letter-spacing:3px}
</style>
</head>
<body>
<div class="flyer">
  <div class="hero" role="img" aria-label="Las Vegas Strip skyline at dusk with illuminated hotels and casinos"></div>

  <div class="compliments">
    <p class="compliments__title">THIS CERTIFICATE IS<br>COMPLIMENTS OF</p>
    <p class="compliments__lines">Certificate Courtesy Of<br>Text Line 2<br>Text Line 3</p>
  </div>

  <div class="exclusive">EXCLUSIVELY FOR : CUSTOMER NAME</div>

  <h1 class="headline">4 Nights Of Resort Casino Accommodations<br>In Las Vegas, NV!</h1>

  <div class="gallery">
    <div class="gallery__photo gallery__photo--sign" role="img" aria-label="Welcome to Las Vegas sign at night with palm trees"></div>
    <div class="gallery__photo gallery__photo--hotel" role="img" aria-label="Neon-lit resort hotel tower at night"></div>
    <div class="gallery__photo gallery__photo--strip" role="img" aria-label="Busy Las Vegas boulevard with traffic and neon lights"></div>
  </div>

  <h2 class="section-title section-title--features">Features:</h2>
  <ul class="features">
    <li>Travel 7 Days A Week</li>
    <li>Stay Your Choice Of Nights (1-4 Nights)</li>
    <li>Good For Two Adults &amp; Two Children</li>
    <li>Pay Just The Taxes &amp; Fees</li>
    <li>Multiple Travel Date Requests Allowed</li>
    <li>Fully Transferable To Another Person</li>
    <li>Just A 30 Days Advance Notice Required</li>
    <li>You Will Have 12 Months To Complete Travel After Redemption</li>
  </ul>

  <h2 class="section-title section-title--how">How Can We Do This?</h2>
  <ul class="reasons">
    <li><svg viewBox="0 0 24 22"><path d="M2 11h16M13 5l6 6-6 6" fill="none" stroke="#5a4a38" stroke-width="2"/></svg>We contract with the world leading hotel chains and resorts to help them fill their otherwise empty rooms.</li>
    <li><svg viewBox="0 0 24 22"><path d="M2 11h16M13 5l6 6-6 6" fill="none" stroke="#5a4a38" stroke-width="2"/></svg>We help fill empty rooms which the hotels, resorts and cruise lines turn into additional revenue from other areas of their property and future bookings.</li>
    <li><svg viewBox="0 0 24 22"><path d="M2 11h16M13 5l6 6-6 6" fill="none" stroke="#5a4a38" stroke-width="2"/></svg>Hotels rarely experience full occupancy, yet they remain open, providing rooms and services at fixed costs. So when hotels give out their rooms by partnering with marketing companies like us, they might miss out on the room fee, but they already didn't have that in the first place, at least now they have the opportunity to gain a customer for their in-house restaurants, room service, their casinos, an extra day stay, future bookings, etc.</li>
  </ul>

  <div class="cta">
    <p class="cta__lead">View all the details of this special offer and</p>
    <p class="cta__link">Redeem online at<br>www.Qotavernix.com</p>
  </div>

  <div class="story">
    <p class="story__text">There is no doubt that Las Vegas is one of the hottest travel destinations around the world. In fact, some people would even go as far as saying that perhaps it is THE hottest place to visit. Enjoy up to 4 nights of resort/casino accommodations in exciting Las Vegas, NV. Millions of people travel to this exciting city each year to enjoy its thrills. Thanks to the business you received this certificate from, now you can enjoy exciting Las Vegas, NV too!</p>
    <div class="certificate">
      <p class="certificate__id">CERTIFICATE ID # 47261-38157<br>EXPIRES 02/29/2020</p>
      <p class="certificate__terms">(Terms and conditions apply see website for details)</p>
    </div>
  </div>

  <footer class="footer">www.Qotavernix.com</footer>
</div>
</body>
</html>
```